Heritage Hollow Business Cards

Require a business card design. <br/><br/>Needs to include logo (either round or long version) plus these details:<br/>Maya Torvell<br/>Heritage Hollow<br/>maya@kelvadtrading.com.au<br/>02 6481 7395<br/>PO Box Glenwarra NSW 2791<br/>www.heritagehollow.com.au<br/><br/>I need in an editable format so that I can create for multiple staff members. <br/><br/>

Target Market(s)

We are an online store selling renovation products to home owners are builders. Looking for a classic classy design.

Industry/Entity Type

Home And Garden

Contact Information for Business Card

Maya Torvell
Heritage Hollow
maya@kelvadtrading.com.au
02 6481 7395
PO Box Glenwarra NSW 2791
www.heritagehollow.com.au

Colors

Designer to choose colors to be used in the design.

Requirements
Must have
• Must include Logo.

```html
<!DOCTYPE html>
<html lang="en">
<head>
<meta charset="utf-8">
<title>Heritage Hollow Business Cards</title>
<link rel="stylesheet" href="https://fonts.googleapis.com/css2?family=Libre+Baskerville&display=swap">
<style>
  :root {
    --backdrop: #1c1d20;
    --card: #25282b;
    --ink: #f1f1f1;
    --ink-soft: #c9cacb;
    --rule: #8c8e90;
  }
  * { margin: 0; padding: 0; box-sizing: border-box; }
  html, body { width: 1200px; height: 800px; overflow: hidden; background: var(--backdrop); }
  body { position: relative; font-family: "Libre Baskerville", Georgia, serif; color: var(--ink); }

  .card {
    position: absolute;
    width: 560px;
    height: 320px;
    background: var(--card);
    box-shadow: 0 18px 40px rgba(0,0,0,0.5);
  }
  .card--front { left: 70px; top: 70px; }
  .card--back { left: 570px; top: 410px; }

  /* Front */
  .front-brand {
    position: absolute;
    left: 70px; top: 0; bottom: 0;
    display: flex; align-items: center; gap: 22px;
  }
  .brand-mark {
    width: 96px; height: 96px;
    border: 1.5px solid var(--ink);
    border-radius: 50%;
    flex: none;
  }
  .front-brand .brand-name { font-size: 38px; letter-spacing: 0.5px; white-space: nowrap; }

  /* Back */
  .back-brand {
    position: absolute;
    left: 40px; top: 80px;
    width: 160px; height: 160px;
    border: 1.5px solid var(--ink);
    border-radius: 50%;
    display: flex; align-items: center; justify-content: center;
    text-align: center;
  }
  .back-brand .brand-name { font-size: 22px; line-height: 1.15; }

  .divider {
    position: absolute;
    left: 250px; top: 70px;
    width: 1px; height: 180px;
    background: linear-gradient(var(--card), var(--rule), var(--card));
  }

  .contact {
    position: absolute;
    left: 282px; top: 78px;
  }
  .contact__name { font-size: 22px; }
  .contact__title { font-size: 11px; color: var(--ink-soft); margin-top: 4px; }
  .contact__list { list-style: none; margin-top: 24px; }
  .contact__item {
    display: flex; align-items: center; gap: 8px;
    font-size: 11.5px; color: var(--ink-soft);
    margin-bottom: 9px; white-space: nowrap;
  }
  .contact__icon {
    width: 15px; height: 15px; flex: none;
  }
</style>
</head>
<body>
  <section class="card card--front" aria-label="Card front">
    <div class="front-brand">
      <span class="brand-mark" aria-hidden="true"></span>
      <span class="brand-name">Heritage Hollow</span>
    </div>
  </section>

  <section class="card card--back" aria-label="Card back">
    <div class="back-brand">
      <span class="brand-name">Heritage<br>Hollow</span>
    </div>
    <div class="divider"></div>
    <div class="contact">
      <p class="contact__name">Maya Torvell</p>
      <p class="contact__title">Managing Director</p>
      <ul class="contact__list">
        <li class="contact__item">
          <svg class="contact__icon" viewBox="0 0 16 16" aria-hidden="true"><circle cx="8" cy="8" r="7" fill="none" stroke="#f1f1f1"/><path d="M5.5 4.5l1.5 0 .6 1.8-1 .7a5 5 0 0 0 2.4 2.4l.7-1 1.8.6v1.5c-3.5.3-6.3-2.5-6-6z" fill="#f1f1f1"/></svg>
          02 6481 7395
        </li>
        <li class="contact__item">
          <svg class="contact__icon" viewBox="0 0 16 16" aria-hidden="true"><circle cx="8" cy="8" r="7" fill="none" stroke="#f1f1f1"/><rect x="4" y="5.5" width="8" height="5.5" fill="none" stroke="#f1f1f1" stroke-width="0.9"/><path d="M4 5.5l4 3 4-3" fill="none" stroke="#f1f1f1" stroke-width="0.9"/></svg>
          maya@kelvadtrading.com.au
        </li>
        <li class="contact__item">
          <svg class="contact__icon" viewBox="0 0 16 16" aria-hidden="true"><circle cx="8" cy="8" r="7" fill="none" stroke="#f1f1f1"/><path d="M8 12.5s-3-3-3-5a3 3 0 0 1 6 0c0 2-3 5-3 5z" fill="#f1f1f1"/><circle cx="8" cy="7.4" r="1" fill="#25282b"/></svg>
          PO Box Glenwarra NSW 2791
        </li>
        <li class="contact__item">
          <svg class="contact__icon" viewBox="0 0 16 16" aria-hidden="true"><circle cx="8" cy="8" r="7" fill="none" stroke="#f1f1f1"/><circle cx="8" cy="8" r="4" fill="none" stroke="#f1f1f1" stroke-width="0.9"/><path d="M4 8h8M8 4c-2 2.2-2 5.8 0 8M8 4c2 2.2 2 5.8 0 8" fill="none" stroke="#f1f1f1" stroke-width="0.8"/></svg>
          www.heritagehollow.com.au
        </li>
      </ul>
    </div>
  </section>
</body>
</html>
```